A website for a Maltese Law Firm

Our law firm needs a website to further its business. The site should have a simple yet effective design. We would need the following sections: About us, Practice Areas, About Malta, Contact. These should be further split as follows:

About us: Our firm, Our values, What others say, Offices

Practice Areas: Crimimal, Citizenship & Residence, Sovereign Patron Pathway, Criminal Defence, Civil Litigation, Arbitration and ADR, Commercial and Corporate, Media Law.

About Malta: just one section.

Contact: Just one section

We would also need a news feed at the front of the site to include latest news regarding our cases.

At the bottom we need a section for our Terms and a Privacy Statement.

Our logo is being attached.

Target Market(s)

All clients looking for legal assistance in Malta

Industry/Entity Type

Legal

Coding

Coded - Design and coding required

Number of Pages Required

1 page

Requirements
Must have
• It must be simple yet striking.

```html
<!DOCTYPE html>
<html lang="en">
<head>
<meta charset="utf-8">
<title>Dravell &amp; Sorrent Advocates</title>
<link href="https://fonts.googleapis.com/css2?family=Libre+Baskerville:wght@400;700&family=Open+Sans:wght@400;600;700&display=swap" rel="stylesheet">
<style>
:root{
  --brown-dark:#3a2117;
  --brown-line:#7a5a4a;
  --ink:#2b1a12;
  --grey-num:#8a7e78;
  --text:#3a3a3a;
  --footer:#1d1d1d;
  --footer-text:#8c8c8c;
  --white:#ffffff;
  --rule:#e2e2e2;
}
*{margin:0;padding:0;box-sizing:border-box}
html,body{width:1200px;height:2174px;overflow:hidden;background:var(--white)}
body{position:relative;font-family:"Libre Baskerville",Georgia,serif;color:var(--text)}
.abs{position:absolute}

/* top bar */
.topbar{left:159px;width:881px;top:0;height:36px;border-bottom:1px solid var(--rule);font-family:"Open Sans",Arial,sans-serif;font-size:11px;color:#444}
.topbar .call{position:absolute;left:0;top:12px}
.topbar .links{position:absolute;right:0;top:12px;display:flex;gap:22px;align-items:center}
.social-dot{width:7px;height:7px;border-radius:50%;background:#444;display:inline-block}

/* header */
.brand{left:159px;top:64px;display:flex;align-items:center;gap:10px;font-size:21px;font-weight:400;color:#1a1a1a;white-space:nowrap}
.brand .mark{width:12px;height:12px;background:#1a1a1a}
.nav{right:162px;top:72px;display:flex;gap:34px;font-size:12px;color:#555;white-space:nowrap}
.nav .active{color:#1a1a1a;font-weight:700}

/* hero */
.hero{left:0;top:122px;width:1200px;height:421px;background:linear-gradient(90deg,#5c4236 0%,#7a5e50 35%,#6b5044 65%,#57402f 100%)}
.hero-band{left:0;top:262px;width:1200px;height:163px;background:rgba(60,35,22,.35)}
.hero-kicker{left:540px;top:300px;font-size:14px;font-weight:700;color:#e9c48f;letter-spacing:.3px}
.hero-title{left:540px;top:324px;font-size:26px;font-weight:700;color:var(--white);line-height:1.18}
.arrow{top:318px}

/* welcome */
.kicker{font-size:14px;font-weight:700;color:#6f5a50;text-align:center;width:1200px;left:0}
.section-title{font-size:27px;font-weight:700;color:var(--ink);text-align:center;width:1200px;left:0;letter-spacing:.5px}
.stat{width:180px;text-align:center}
.stat .num{font-family:"Open Sans",Arial,sans-serif;font-weight:700;font-size:28px;color:var(--grey-num);line-height:1}
.stat .label{font-size:12px;color:#2a2a2a;margin-top:12px}
.divider-v{left:517px;top:700px;width:1px;height:239px;background:var(--rule)}
.about{left:584px;top:728px;width:456px}
.about .eyebrow{font-size:12px;font-weight:700;color:#1a1a1a;letter-spacing:.3px}
.about h2{font-size:25px;font-weight:700;color:#1a1a1a;margin-top:8px;white-space:nowrap}
.about p{font-size:10px;line-height:17px;color:#444;margin-top:14px}
.btn{display:inline-flex;align-items:center;gap:12px;margin-top:20px;background:var(--brown-dark);color:var(--white);font-size:10px;font-weight:700;padding:0 18px;height:36px;white-space:nowrap}

/* practice */
.practice-photo{left:0;top:1003px;width:430px;height:449px;background:linear-gradient(160deg,#e9e6e2 0%,#cfc7bf 45%,#5a4a40 100%)}
.practice{left:430px;top:1003px;width:770px;height:449px;background:var(--brown-dark)}
.practice h2{position:absolute;left:38px;top:54px;font-size:26px;font-weight:700;color:var(--white);letter-spacing:.3px}
.practice p{position:absolute;left:38px;top:98px;width:600px;font-size:9.5px;line-height:16px;color:#e8ddd6}
.area{position:absolute;width:277px;height:40px;border:1px solid var(--brown-line);display:flex;align-items:center;padding-left:14px;font-size:11.5px;color:#e9dfd8;white-space:nowrap}
.area .plus{position:absolute;right:0;top:0;width:43px;height:38px;background:rgba(0,0,0,.22);display:flex;align-items:center;justify-content:center}

/* news */
.news{width:290px;top:1600px;display:flex;gap:16px}
.news .thumb{width:102px;height:92px;flex:none;background:linear-gradient(135deg,#c9b8a8,#6e5446)}
.news h3{font-family:"Open Sans",Arial,sans-serif;font-size:11.5px;font-weight:700;color:#1a1a1a;line-height:15px;text-transform:uppercase}
.news .date{font-family:"Open Sans",Arial,sans-serif;font-size:11px;color:#1a1a1a;margin-top:2px}
.news p{font-family:"Open Sans",Arial,sans-serif;font-size:10.5px;line-height:15px;color:#999;margin-top:6px}
.dots{left:583px;top:1726px;display:flex;gap:5px}
.dots span{width:5px;height:5px;border-radius:50%;background:#ccc}
.dots span.on{background:#333}

/* footer */
.footer{left:0;top:1792px;width:1200px;height:382px;background:var(--footer);font-family:"Open Sans",Arial,sans-serif;color:var(--footer-text)}
.footer h4{position:absolute;font-family:"Libre Baskerville",Georgia,serif;font-weight:400;font-size:17px;color:var(--white)}
.footer .tick{position:absolute;width:16px;height:2px;background:var(--white)}
.footer .vline{position:absolute;left:522px;top:0;width:1px;height:305px;background:#3a3a3a}
.footer .vdot{position:absolute;left:518px;top:305px;width:9px;height:9px;border-radius:50%;border:1px solid #555}
.footer .hline{position:absolute;left:160px;top:219px;width:362px;height:1px;background:#3a3a3a}
.terms{position:absolute;left:164px;top:126px;width:310px;font-size:11.5px;line-height:18px}
.copy{position:absolute;left:164px;top:246px;font-size:10px;line-height:17px}
.fsocial{position:absolute;left:164px;top:298px;display:flex;gap:22px}
.fsocial span{width:7px;height:7px;border-radius:50%;background:#8c8c8c}
.contact-list{position:absolute;left:588px;top:126px;font-size:11px;line-height:22.5px;color:#bbb}
.contact-list div{display:flex;align-items:center;gap:12px}
.addr{position:absolute;left:588px;top:240px;display:flex;gap:14px;font-size:10.5px;line-height:14px;color:#bbb}
.map{position:absolute;left:788px;top:71px;width:251px;height:206px;background:linear-gradient(135deg,#e6e6e6,#cfcfcf)}
</style>
</head>
<body>

<div class="abs topbar">
  <span class="call">Call Us: (356) 2000 14 80</span>
  <div class="links"><span>Contact</span><span>FAQ</span>
    <span style="display:flex;gap:14px"><i class="social-dot"></i><i class="social-dot"></i><i class="social-dot"></i><i class="social-dot"></i></span>
  </div>
</div>

<div class="abs brand"><span class="mark"></span>Dravell &amp; Sorrent</div>
<nav class="abs nav"><span class="active">Home</span><span>About Us</span><span>Practice Areas</span><span>About Malta</span><span>Contact Us</span></nav>

<div class="abs hero" role="img" aria-label="Smiling lawyer holding a red folder in front of classical stone columns"></div>
<div class="abs hero-band"></div>
<div class="abs hero-kicker">DS ADVOCATES</div>
<div class="abs hero-title">We are a law firm<br>from Malta</div>
<svg class="abs arrow" style="left:36px" width="20" height="40" viewBox="0 0 20 40"><path d="M17 2 L3 20 L17 38" fill="none" stroke="#fff" stroke-width="1.5"/></svg>
<svg class="abs arrow" style="left:1144px" width="20" height="40" viewBox="0 0 20 40"><path d="M3 2 L17 20 L3 38" fill="none" stroke="#fff" stroke-width="1.5"/></svg>

<div class="abs kicker" style="top:590px">DS ADVOCATES</div>
<div class="abs section-title" style="top:620px">WELCOME TO OUR SITE</div>

<div class="abs stat" style="left:152px;top:731px"><div class="num">348+</div><div class="label">Trusted Clients</div></div>
<div class="abs stat" style="left:339px;top:731px"><div class="num">$2834.00</div><div class="label">Money Paids</div></div>
<div class="abs stat" style="left:152px;top:843px"><div class="num">99%</div><div class="label">Successful Case</div></div>
<div class="abs stat" style="left:339px;top:843px"><div class="num">38520</div><div class="label">Case Closed</div></div>
<div class="abs divider-v"></div>

<div class="abs about">
  <div class="eyebrow">ABOUT THE FIRM</div>
  <h2>We are a law firm from Malta</h2>
  <p>Lorem ipsum dolor sit amet, consectetur adipiscing elit. Proin eu vulputate orci. Sed porttitor laoreet quam, a sollicitudin leo congue id. In et nisl convallis, vulputate risus a, mollis ante. Sed lobortis leo ex, lacinia finibus massa vulputate ac. Pellentesque convallis justo ut eros iaculis, at fermentum augue vehicula.</p>
  <div class="btn">READ MORE
    <svg width="14" height="14" viewBox="0 0 14 14"><circle cx="7" cy="7" r="7" fill="#fff"/><path d="M5.5 4 L8.5 7 L5.5 10" fill="none" stroke="#3a2117" stroke-width="1.6"/></svg>
  </div>
</div>

<div class="abs practice-photo" role="img" aria-label="Lawyer in a suit holding a leather folder, colleagues at a meeting table behind"></div>
<section class="abs practice">
  <h2>OUR PRACTICE AREAS</h2>
  <p>Lorem ipsum dolor sit amet, consectetur adipiscing elit. Proin eu vulputate orci. Sed porttitor laoreet quam, a sollicitudin leo congue id. In et nisl convallis, vulputate risus a, mollis ante. Sed lobortis leo ex, lacinia finibus massa vulputate ac. Pellentesque convallis justo ut eros iaculis, at fermentum augue vehicula.</p>
  <div class="area" style="left:39px;top:172px">Crimimal<span class="plus"><svg width="14" height="14"><path d="M7 0V14M0 7H14" stroke="#d9ccc4" stroke-width="1.2"/></svg></span></div>
  <div class="area" style="left:331px;top:172px">Citizenship &amp; Residence<span class="plus"><svg width="14" height="14"><path d="M7 0V14M0 7H14" stroke="#d9ccc4" stroke-width="1.2"/></svg></span></div>
  <div class="area" style="left:39px;top:229px">Sovereign Patron Pathway<span class="plus"><svg width="14" height="14"><path d="M7 0V14M0 7H14" stroke="#d9ccc4" stroke-width="1.2"/></svg></span></div>
  <div class="area" style="left:331px;top:229px">Criminal Defence<span class="plus"><svg width="14" height="14"><path d="M7 0V14M0 7H14" stroke="#d9ccc4" stroke-width="1.2"/></svg></span></div>
  <div class="area" style="left:39px;top:285px">Civil Litigation<span class="plus"><svg width="14" height="14"><path d="M7 0V14M0 7H14" stroke="#d9ccc4" stroke-width="1.2"/></svg></span></div>
  <div class="area" style="left:331px;top:285px">Arbitration and ADR<span class="plus"><svg width="14" height="14"><path d="M7 0V14M0 7H14" stroke="#d9ccc4" stroke-width="1.2"/></svg></span></div>
  <div class="area" style="left:39px;top:342px">Commercial and Corporate<span class="plus"><svg width="14" height="14"><path d="M7 0V14M0 7H14" stroke="#d9ccc4" stroke-width="1.2"/></svg></span></div>
  <div class="area" style="left:331px;top:342px">Media Law<span class="plus"><svg width="14" height="14"><path d="M7 0V14M0 7H14" stroke="#d9ccc4" stroke-width="1.2"/></svg></span></div>
</section>

<div class="abs section-title" style="top:1526px">LATEST NEWS</div>

<article class="abs news" style="left:160px">
  <div class="thumb" role="img" aria-label="Businesswoman giving a thumbs up"></div>
  <div><h3>Lorem ipsum dolor sit ectetur adipiscin</h3><div class="date">18-09-2016</div><p>Nullam quis justo a justo varius lore dignissim ut sed elit. lorem Suspendisse potenti.</p></div>
</article>
<article class="abs news" style="left:467px">
  <div class="thumb" role="img" aria-label="Two people consulting over documents"></div>
  <div><h3>Lorem ipsum dolor sit ectetur adipiscin</h3><div class="date">18-09-2016</div><p>Nullam quis justo a justo varius lore dignissim ut sed elit. lorem Suspendisse potenti.</p></div>
</article>
<article class="abs news" style="left:767px">
  <div class="thumb" role="img" aria-label="Colleagues reviewing a contract at a desk"></div>
  <div><h3>Lorem ipsum dolor sit ectetur adipiscin</h3><div class="date">18-09-2016</div><p>Nullam quis justo a justo varius lore dignissim ut sed elit. lorem Suspendisse potenti.</p></div>
</article>
<div class="abs dots"><span class="on"></span><span></span><span></span><span></span></div>

<footer class="abs footer">
  <div class="vline"></div><div class="vdot"></div><div class="hline"></div>
  <h4 style="left:164px;top:68px">Terms and a Privacy Statement</h4>
  <div class="tick" style="left:164px;top:101px"></div>
  <p class="terms">Lorem ipsum dolor sit amet, consectetur&nbsp; some dymmy adipiscing elit. Nam turpis quam, sodales in text she ante sagittis, varius efficitur mauris. Nam turpis quam, sodales in text should be able. to...</p>
  <div class="copy">©Copyright 2016 yoursite. All Rights Reserved.<br>Privacy Policy &nbsp;|&nbsp; Terms &amp; Conditions</div>
  <div class="fsocial"><span></span><span></span><span></span><span></span></div>

  <h4 style="left:588px;top:68px">Location</h4>
  <div class="tick" style="left:588px;top:101px"></div>
  <div class="contact-list">
    <div><svg width="9" height="9" viewBox="0 0 10 10"><path d="M2 0.5 L4 3 L3 4.2 Q4.5 6.5 6 7 L7.2 6 L9.5 8 L8 9.6 Q3 9 0.5 2 Z" fill="#999"/></svg>(356) 2000 7712(Valletta)</div>
    <div><svg width="9" height="9" viewBox="0 0 10 10"><path d="M2 0.5 L4 3 L3 4.2 Q4.5 6.5 6 7 L7.2 6 L9.5 8 L8 9.6 Q3 9 0.5 2 Z" fill="#999"/></svg>(356) 2000 7712(Birkirkara)</div>
    <div><svg width="9" height="9" viewBox="0 0 10 10"><path d="M2 0.5 L4 3 L3 4.2 Q4.5 6.5 6 7 L7.2 6 L9.5 8 L8 9.6 Q3 9 0.5 2 Z" fill="#999"/></svg>(356) 2000 3390</div>
    <div><svg width="9" height="9" viewBox="0 0 10 10"><rect x="0.5" y="2" width="9" height="6.5" fill="#999"/><path d="M0.5 2 L5 5.5 L9.5 2" fill="none" stroke="#1d1d1d"/></svg>info@dravellsorrent.com</div>
  </div>
  <div class="addr">
    <svg width="8" height="11" viewBox="0 0 8 11" style="margin-top:2px"><path d="M4 11 L0.6 5 A3.8 3.8 0 1 1 7.4 5 Z" fill="#999"/><circle cx="4" cy="3.8" r="1.3" fill="#1d1d1d"/></svg>
    <div>12/4, Harbour Lane,<br>VLT 1010, Valletta<br>Southern Harbour<br>Malta</div>
  </div>
  <div class="map" role="img" aria-label="Street map showing the office location"></div>
</footer>

</body>
</html>
```